Business card for denture clinic Veltrimora

We need a new business card with our new logo. We are a denture clinic in New Zealand with our target market being 45+ years old. We would need a space on the back to write our patients next appointment on. We would space for only one appointment rather than a list. We will attach a photo showing an example of this. But of course, we would like to see your twist on this. We want it to be bold and easy to read and a good mixture of professional but modern. We have attached our logo to be used on the card.

Target Market(s)

People aged 45+ needing dentures

Industry/Entity Type

Dental

Contact Information for Business Card

We want our logo on the front and the space to write an appointment on the back. I've attached an example our our old business card showing this. We need to have the technicians details on the front.

Font styles to use
Sans Serif

Colors
0255a3
919191
fbfbfb

Requirements
Must have
• The following details:
• Liam Dorsett BDT, PGDipCDentTech Calverin
• Dental Prosthetist
• Phone numbers: 0800 47 3125
• 09 572 1394
• Email: liam@veltrimora.co.nz
• www.veltrimora.co.nz
• Address: 14 Marlow Crest Road
• Halbrook West
• Auckland 0793
Nice to have
• We would like our business cards to have more than just two colours as we want them to be more vibrant. We have uploaded an example of a business card we liked that showed this.

```html
<!DOCTYPE html>
<html lang="en">
<head>
<meta charset="utf-8">
<title>Veltrimora business card</title>
<link href="https://fonts.googleapis.com/css2?family=Open+Sans:ital,wght@0,400;0,600;0,700;1,400&display=swap" rel="stylesheet">
<style>
  :root {
    --brand-blue: #0270bb;
    --deep-blue: #0255a3;
    --grey: #919191;
    --ink: #444444;
    --paper: #fbfbfb;
    --backdrop: #e9e6e1;
    --white: #ffffff;
  }
  * { margin: 0; padding: 0; box-sizing: border-box; }
  html, body { width: 1200px; height: 987px; overflow: hidden; }
  body {
    background: var(--backdrop);
    font-family: "Open Sans", Arial, sans-serif;
    position: relative;
  }
  .card {
    position: absolute;
    left: 293px;
    width: 615px;
    height: 352px;
    border-radius: 20px;
    overflow: hidden;
    box-shadow: 0 3px 8px rgba(0,0,0,0.25);
  }
  .card--front { top: 130px; background: var(--white); }
  .card--back { top: 505px; background: var(--brand-blue); }

  .name-tab {
    position: absolute; left: 0; top: 23px;
    width: 12px; height: 73px;
    background: var(--brand-blue);
    border-radius: 0 10px 10px 0;
  }
  .tech-name {
    position: absolute; left: 32px; top: 24px;
    color: var(--brand-blue); font-weight: 600; font-size: 21px; line-height: 1.2;
  }
  .tech-name .postnominal { font-size: 15px; }
  .tech-qual {
    position: absolute; left: 32px; top: 53px;
    color: var(--brand-blue); font-weight: 600; font-size: 16px;
  }
  .tech-role {
    position: absolute; left: 30px; top: 77px;
    color: var(--grey); font-size: 16px;
  }
  .divider {
    position: absolute; left: 32px; width: 540px;
    max-width: 246px; border-top: 2px dotted #6a6a6a;
  }
  .divider--top { top: 107px; }
  .divider--bottom { top: 213px; }
  .contact-list {
    position: absolute; left: 33px; top: 114px;
    list-style: none; font-size: 15px; line-height: 23px; color: var(--ink);
  }
  .contact-list .label { color: var(--brand-blue); font-weight: 700; }
  .address {
    position: absolute; left: 33px; top: 221px;
    font-size: 15px; line-height: 23px; color: var(--ink); font-style: normal;
  }
  .brand {
    position: absolute; text-align: center;
  }
  .brand-name {
    font-weight: 600; letter-spacing: 2px; line-height: 1;
  }
  .brand-tagline {
    font-size: 13px; letter-spacing: 3px; line-height: 1; margin-top: 6px;
  }
  .card--front .brand { left: 32px; top: 286px; width: 320px; }
  .card--front .brand-name { font-size: 31px; color: var(--brand-blue); }
  .card--front .brand-tagline { color: var(--grey); }

  .front-emblem {
    position: absolute; left: 315px; top: 45px;
  }

  .card--back .brand-mark {
    position: absolute; left: 280px; top: 53px;
    width: 56px; height: 56px; background: var(--white);
  }
  .card--back .brand { left: 0; top: 123px; width: 615px; }
  .card--back .brand-name { font-size: 29px; color: var(--white); }
  .card--back .brand-tagline { color: var(--paper); font-size: 12px; }
  .appointment-title {
    position: absolute; left: 0; top: 202px; width: 615px;
    text-align: center; color: var(--white); font-weight: 600; font-size: 23px;
  }
  .appointment-field {
    position: absolute; top: 273px; width: 241px; height: 43px;
    background: #f4f4f4; border-radius: 22px;
    padding-left: 17px; line-height: 43px;
    color: var(--brand-blue); font-style: italic; font-size: 17px;
  }
  .appointment-field--date { left: 29px; }
  .appointment-field--time { left: 346px; }
</style>
</head>
<body>
  <section class="card card--front" aria-label="Card front">
    <div class="name-tab"></div>
    <h1 class="tech-name">LIAM DORSETT <span class="postnominal">BDT,</span></h1>
    <p class="tech-qual">PGDipCDentTech Calverin</p>
    <p class="tech-role">Dental Prosthetist</p>
    <div class="divider divider--top"></div>
    <ul class="contact-list">
      <li><span class="label">P :</span> 0800 47 3125</li>
      <li><span class="label">C :</span> 09 572 1394</li>
      <li>liam@veltrimora.co.nz</li>
      <li>www.veltrimora.co.nz</li>
    </ul>
    <div class="divider divider--bottom"></div>
    <address class="address">14 Marlow Crest Road<br>Halbrook West, Auckland 0793</address>
    <div class="brand">
      <div class="brand-name">VELTRIMORA</div>
      <div class="brand-tagline">THE DENTURE EXPERTS</div>
    </div>
    <svg class="front-emblem" width="280" height="280" viewBox="0 0 280 280" aria-hidden="true">
      <circle cx="140" cy="140" r="120" fill="none" stroke="var(--brand-blue)" stroke-width="22"/>
    </svg>
  </section>

  <section class="card card--back" aria-label="Card back">
    <div class="brand-mark"></div>
    <div class="brand">
      <div class="brand-name">VELTRIMORA</div>
      <div class="brand-tagline">THE DENTURE EXPERTS</div>
    </div>
    <h2 class="appointment-title">Next Appointment</h2>
    <div class="appointment-field appointment-field--date">date:</div>
    <div class="appointment-field appointment-field--time">time:</div>
  </section>
</body>
</html>
```